I need a label with logo to go on jars of honey.
Label size 70mm x 70mm
The front label should say :
The Fenwick Honey Co. (logo)
Tarapeka Honey
400g
The back label:
Would have nutritional information
And our address
You can see from the uploaded files the styles I prefer, I have uploaded a photo of the honey product too. The background of the logo doesn't have to be white. I would like to develop a color scheme that would look nice against the color of the honey.
Logo Text
The Fenwick Honey Co. / The Fenwick Honey Company

```html
<!DOCTYPE html>
<html lang="en">
<head>
<meta charset="utf-8">
<title>The Fenwick Honey Co. – Tarapeka Honey jar labels</title>
<link rel="stylesheet" href="https://fonts.googleapis.com/css2?family=Oswald:wght@400;500&family=Montserrat:wght@400&family=Yellowtail&family=Playball&family=Parisienne&display=swap">
<style>
  :root {
    --page: #ffffff;
    --frame: #9a9a9a;
    --paper: #f2f2f2;
    --paper-warm: #f3f2ee;
    --plum: #8e3c63;
    --plum-deep: #a2325a;
    --mauve: #a06282;
    --teal: #38b5aa;
    --gold: #f5be00;
    --amber: #f5a200;
    --mustard: #d6b000;
    --rose: #b23a68;
    --sun: #f2cc1c;
    --bark: #8a4a1d;
    --ink: #3b3b3b;
    --white: #ffffff;
  }
  html, body { margin: 0; padding: 0; overflow: hidden; background: var(--page); }
  .sheet { display: block; width: 1200px; height: 1191px; }
  .frame { fill: none; stroke: var(--frame); stroke-width: 2; }
  .label-title { font-family: "Oswald", sans-serif; font-weight: 500; text-anchor: middle; }
  .label-variety { font-family: "Oswald", sans-serif; font-weight: 500; text-anchor: middle; }
  .script-line { font-family: "Playball", cursive; text-anchor: middle; }
  .script-title { font-family: "Yellowtail", cursive; text-anchor: middle; }
  .script-variety { font-family: "Parisienne", cursive; text-anchor: middle; }
  .tagline { font-family: "Montserrat", sans-serif; font-size: 17px; text-anchor: middle; letter-spacing: 0.5px; }
  .weight { font-family: "Oswald", sans-serif; font-weight: 500; text-anchor: middle; }
  .weight-light { font-family: "Montserrat", sans-serif; text-anchor: middle; }
  .card-title { font-family: "Oswald", sans-serif; font-weight: 500; fill: var(--bark); }
</style>
</head>
<body>
<svg class="sheet" viewBox="0 0 1200 1191" xmlns="http://www.w3.org/2000/svg">
  <rect class="frame" x="1" y="1" width="1198" height="1189"/>

  <!-- Label A: plum and gold -->
  <g class="label label-plum-gold">
    <rect x="33" y="55" width="523" height="522" fill="var(--paper)"/>
    <rect x="33" y="67" width="523" height="23" fill="var(--plum)"/>
    <rect x="33" y="398" width="523" height="179" fill="var(--plum)"/>
    <rect class="brand-mark" x="262" y="165" width="60" height="60" fill="var(--gold)"/>
    <text class="label-title" x="295" y="297" font-size="52" fill="var(--plum)" textLength="410" lengthAdjust="spacingAndGlyphs">THE FENWICK HONEY CO.</text>
    <text class="label-variety" x="295" y="357" font-size="52" fill="var(--gold)" textLength="300" lengthAdjust="spacingAndGlyphs">TARAPEKA HONEY</text>
    <circle class="badge" cx="294" cy="409" r="37" fill="var(--white)" stroke="#2e6b35" stroke-width="5"/>
    <text class="script-line" x="295" y="482" font-size="27" fill="var(--white)">Pure &amp; Gold Honey</text>
    <text class="tagline" x="295" y="518" fill="var(--white)">— NATURAL TASTE —</text>
    <text class="weight-light" x="295" y="558" font-size="16" fill="var(--white)">400g</text>
  </g>

  <!-- Label B: teal and rose -->
  <g class="label label-teal-rose">
    <rect x="634" y="55" width="522" height="522" fill="var(--paper)"/>
    <rect x="634" y="55" width="522" height="167" fill="var(--teal)"/>
    <rect x="634" y="221" width="522" height="4" fill="var(--amber)"/>
    <rect x="634" y="520" width="522" height="57" fill="var(--teal)"/>
    <rect class="brand-mark" x="850" y="95" width="90" height="90" fill="var(--rose)"/>
    <text class="script-title" x="895" y="318" font-size="70" fill="var(--mustard)" textLength="420" lengthAdjust="spacingAndGlyphs">The Fenwick Honey Co</text>
    <text class="label-variety" x="897" y="396" font-size="38" fill="var(--rose)" text-anchor="end" style="text-anchor:end">TARAPEKA</text>
    <g role="img" aria-label="Illustration of a honey dipper dripping into a small bowl of honey with a daisy">
      <rect x="904" y="330" width="26" height="66" rx="12" fill="var(--amber)" opacity="0.8"/>
      <ellipse cx="897" cy="422" rx="26" ry="16" fill="var(--amber)" opacity="0.8"/>
    </g>
    <text class="label-variety" x="937" y="396" font-size="38" fill="var(--rose)" style="text-anchor:start">HONEY</text>
    <text class="script-line" x="895" y="472" font-size="26" fill="var(--teal)">Pure &amp; Gold Honey</text>
    <text class="tagline" x="895" y="503" fill="var(--amber)">— NATURAL TASTE —</text>
    <text class="weight" x="895" y="556" font-size="22" fill="var(--ink)">400G</text>
  </g>

  <!-- Label C: plum and amber -->
  <g class="label label-plum-amber">
    <rect x="33" y="612" width="523" height="522" fill="var(--paper)"/>
    <rect x="33" y="612" width="523" height="211" fill="var(--plum)"/>
    <circle class="brand-mark" cx="296" cy="725" r="55" fill="var(--gold)"/>
    <text class="label-title" x="295" y="903" font-size="62" fill="var(--plum-deep)" textLength="430" lengthAdjust="spacingAndGlyphs">THE FENWICK HONEY CO.</text>
    <text class="label-variety" x="295" y="965" font-size="55" fill="var(--amber)" textLength="300" lengthAdjust="spacingAndGlyphs">TARAPEKA HONEY</text>
    <rect x="252" y="990" width="90" height="70" rx="22" fill="#f0b43a" role="img" aria-label="Illustration of a honey pot with daisies"/>
    <text class="weight" x="288" y="1097" font-size="22" fill="var(--ink)">400G</text>
    <rect x="43" y="1117" width="503" height="17" fill="var(--mauve)" role="img" aria-label="Decorative border of small hexagons"/>
  </g>

  <!-- Label D: paper and sun card -->
  <g class="label label-paper-sun">
    <rect x="618" y="612" width="522" height="522" fill="var(--paper-warm)"/>
    <g class="title-card" transform="translate(879 789) rotate(-13)">
      <rect x="-215" y="-125" width="430" height="250" fill="var(--sun)"/>
      <text class="card-title" x="-150" y="-30" font-size="62" textLength="300" lengthAdjust="spacingAndGlyphs">THE FENWICK</text>
      <text class="card-title" x="-150" y="42" font-size="82" textLength="235" lengthAdjust="spacingAndGlyphs">HONEY</text>
      <text class="card-title" x="-150" y="90" font-size="46" textLength="225" lengthAdjust="spacingAndGlyphs">COMPANY</text>
      <ellipse cx="160" cy="42" rx="36" ry="26" fill="#e7b02a" opacity="0.8" role="img" aria-label="Illustration of a small bee"/>
    </g>
    <g role="img" aria-label="Sketch of a honey dipper with a pool of honey">
      <rect x="866" y="922" width="24" height="58" rx="10" fill="#e6c48a" opacity="0.75"/>
      <ellipse cx="893" cy="1051" rx="40" ry="8" fill="#e6c48a" opacity="0.75"/>
    </g>
    <text class="script-variety" x="880" y="1025" font-size="48" fill="var(--ink)">Tarapeka Honey</text>
    <text class="weight" x="895" y="1102" font-size="22" fill="var(--ink)">400G</text>
    <rect x="628" y="1117" width="502" height="17" fill="var(--ink)" role="img" aria-label="Decorative border of small hexagons"/>
  </g>
</svg>
</body>
</html>
```